****Modern, Urban & Professional Business card for electrical company (electrician

Require a business card for an electrical company providing electrician services. Specifically residential and commercial property.

Business card must represent the company and brand and use the company colours in some way whether that be just the logo & name or full colour. Would like icons to be used for social media platforms email and telephone. Open to use of QR code but don’t want the card to look too busy.
QR Code must link to contact details on phone. Add contact with Name, Company, Phone Number, Website on phone contact details.

If you are a designer working on this job we would appreciate if you could follow our social media channels in exchange for a follow back. As a small start up business every like/follow helps :)

Would like to make the business card into a magnet (single sided also) future project

Industry/Entity Type

Electrician

Contact Information for Business Card

Colours to include but not limited to
dark blue -142455
sky blue - 0094da

91 x 55 mm size

Information to include:

Dean Whitcombe
Director
0215567391

www.brightwirepower.co.nz
info@brightwirepower.co.nz
www.Facebook.com/brightwirepower
www.instagram.com/brightwire.power

Might be good to add:
24 hour emergency service

Requirements
Must have
• Email address included on card

```html
<!DOCTYPE html>
<html lang="en">
<head>
<meta charset="utf-8">
<title>Brightwire Power – Business Card</title>
<link href="https://fonts.googleapis.com/css2?family=Open+Sans:ital,wght@0,400;0,600;0,700;1,700&display=swap" rel="stylesheet">
<style>
  :root {
    --navy: #1e2456;
    --sky: #1b93d4;
    --card-blue: #1473bf;
    --ink: #3c3c44;
    --paper: #ffffff;
    --backdrop: #e9e6e1;
  }
  * { margin: 0; padding: 0; box-sizing: border-box; }
  html, body {
    width: 900px; height: 1200px; overflow: hidden;
    background: var(--backdrop);
    font-family: "Open Sans", Arial, sans-serif;
  }
  .canvas { position: relative; width: 900px; height: 1200px; }

  .card {
    position: absolute; left: 86px; width: 735px; height: 430px;
    overflow: hidden;
    box-shadow: 0 6px 18px rgba(0,0,0,0.18);
  }
  .card--front { top: 137px; background: var(--paper); }
  .card--back { top: 633px; background: var(--card-blue); }

  /* brand lockup */
  .brand { position: absolute; display: flex; align-items: center; }
  .brand__disc { border-radius: 50%; flex: none; }
  .brand__name {
    font-weight: 700; line-height: 1.05; letter-spacing: 0.3px;
    text-transform: uppercase; white-space: nowrap;
  }
  .card--front .brand { left: 335px; top: 54px; }
  .card--front .brand__disc { width: 112px; height: 112px; background: var(--navy); margin-right: 10px; }
  .card--front .brand__name { font-size: 33px; color: var(--navy); }

  .card--back .brand { left: 126px; top: 119px; }
  .card--back .brand__disc { width: 156px; height: 156px; background: var(--navy); margin-right: 12px; }
  .card--back .brand__name { font-size: 47px; color: #ffffff; }

  .watermark-disc { position: absolute; border-radius: 50%; }
  .card--front .watermark-disc {
    left: 478px; top: 205px; width: 240px; height: 240px;
    background: rgba(30,36,86,0.04);
  }
  .card--back .watermark-disc {
    left: 355px; top: 60px; width: 270px; height: 270px;
    background: rgba(255,255,255,0.07);
  }

  /* person */
  .person { position: absolute; left: 53px; top: 220px; }
  .person__name { font-size: 28px; font-weight: 700; color: var(--navy); line-height: 1.2; }
  .person__role { font-size: 17px; color: var(--ink); margin-top: 1px; }

  .contact-list { position: absolute; list-style: none; }
  .contact-list li {
    display: flex; align-items: center; height: 28px;
    font-size: 17px; color: var(--ink);
  }
  .contact-list--main { left: 53px; top: 302px; }
  .contact-list--main svg { width: 13px; height: 13px; margin-right: 10px; fill: var(--sky); }
  .contact-list--social { left: 497px; top: 330px; }
  .social-dot {
    width: 17px; height: 17px; border-radius: 50%; margin-right: 16px; flex: none;
  }
  .social-dot--first { background: var(--navy); }
  .social-dot--second { background: #6b4a43; }

  .accent-bar { position: absolute; bottom: 0; height: 15px; }
  .accent-bar--sky { left: 0; width: 424px; background: var(--sky); }
  .accent-bar--navy { left: 432px; right: 0; background: var(--navy); }

  .tagline {
    position: absolute; left: 0; right: 0; top: 364px;
    text-align: center; color: #ffffff;
    font-size: 20px; font-weight: 700; font-style: italic; letter-spacing: 0.3px;
  }
</style>
</head>
<body>
<main class="canvas">

  <section class="card card--front" aria-label="Card front">
    <div class="watermark-disc"></div>
    <div class="brand">
      <span class="brand__disc"></span>
      <span class="brand__name">Brightwire<br>Power</span>
    </div>

    <div class="person">
      <p class="person__name">Dean Whitcombe</p>
      <p class="person__role">Director</p>
    </div>

    <ul class="contact-list contact-list--main">
      <li>
        <svg viewBox="0 0 24 24" aria-hidden="true"><path d="M6.6 10.8a15.2 15.2 0 0 0 6.6 6.6l2.2-2.2a1 1 0 0 1 1-.25 11.4 11.4 0 0 0 3.6.57 1 1 0 0 1 1 1V20a1 1 0 0 1-1 1A17 17 0 0 1 3 4a1 1 0 0 1 1-1h3.5a1 1 0 0 1 1 1c0 1.25.2 2.45.57 3.57a1 1 0 0 1-.25 1z"/></svg>
        0215567391
      </li>
      <li>
        <svg viewBox="0 0 24 24" aria-hidden="true"><path d="M2 5h20v2l-10 6L2 7z"/><path d="M2 9l10 6 10-6v10H2z"/></svg>
        info@brightwirepower.co.nz
      </li>
      <li>
        <svg viewBox="0 0 24 24" aria-hidden="true"><path d="M12 2a10 10 0 1 0 0 20 10 10 0 0 0 0-20zm0 2c.9 0 2.1 1.8 2.6 5H9.4C9.9 5.8 11.1 4 12 4zM4.3 11h3a17 17 0 0 0 0 2h-3a8 8 0 0 1 0-2zm5 0h5.4a15 15 0 0 1 0 2H9.3a15 15 0 0 1 0-2zm7.4 0h3a8 8 0 0 1 0 2h-3a17 17 0 0 0 0-2zM9.4 15h5.2c-.5 3.2-1.7 5-2.6 5s-2.1-1.8-2.6-5z"/></svg>
        www.brightwirepower.co.nz
      </li>
    </ul>

    <ul class="contact-list contact-list--social">
      <li><span class="social-dot social-dot--first"></span>brightwirepower</li>
      <li><span class="social-dot social-dot--second"></span>brightwire.power</li>
    </ul>

    <span class="accent-bar accent-bar--sky"></span>
    <span class="accent-bar accent-bar--navy"></span>
  </section>

  <section class="card card--back" aria-label="Card back">
    <div class="watermark-disc"></div>
    <div class="brand">
      <span class="brand__disc"></span>
      <span class="brand__name">Brightwire<br>Power</span>
    </div>
    <p class="tagline">24 hour emergency service</p>
  </section>

</main>
</body>
</html>
```